Quorva - corporate Business Card

We need a good look and innovative business card for a new start up company based in Los Angeles called "Quorva". We are in a payment business, including payment card, app, and ewallet. We are expert in online payment and Card not present (CNP) transaction.
We need an innovative, modern business card.

Our logo font is Aero Matics

Target Market(s)

Startup - Bank - Online Payment - Card Manufacturing

Industry/Entity Type

Startup

Contact Information for Business Card

phone: 555 014 7396 - Address: 4172 Marlowe blvd, Halden City, CA 90299

Requirements
Must have
• Message: innovative, professional, expert, high tech, trust, online payment expert, security
Nice to have
• no comment
Should not have
• no Comment

```html
<!DOCTYPE html>
<html lang="en">
<head>
<meta charset="utf-8">
<title>Quorva business card</title>
<link rel="stylesheet" href="https://fonts.googleapis.com/css2?family=Lato:wght@400;700;900&display=swap">
<style>
  :root {
    --brand-red: #b31d2b;
    --card-white: #f6f6f6;
    --page-bg: #ececec;
    --ink-white: #ffffff;
  }
  * { margin: 0; padding: 0; box-sizing: border-box; }
  html, body { width: 1200px; height: 586px; overflow: hidden; }
  body {
    background: var(--page-bg);
    font-family: "Lato", Arial, sans-serif;
    position: relative;
  }
  .card {
    position: absolute;
    top: 129px;
    width: 501px;
    height: 300px;
    background: var(--card-white);
    overflow: hidden;
  }
  .card-front { left: 61px; }
  .card-back { left: 619px; }

  .brand { position: absolute; display: flex; align-items: center; }
  .brand-dot { border-radius: 50%; background: var(--brand-red); flex: none; }
  .brand-name { color: var(--brand-red); font-weight: 700; line-height: 1; white-space: nowrap; }

  .card-front .brand { left: 76px; top: 81px; }
  .card-front .brand-dot { width: 106px; height: 106px; margin-right: 24px; }
  .card-front .brand-name { font-size: 74px; letter-spacing: 1px; }

  .front-stripe { position: absolute; left: 0; width: 100%; background: var(--brand-red); }
  .front-stripe.thin-1 { top: 254px; height: 3px; }
  .front-stripe.thin-2 { top: 260px; height: 3px; }
  .front-band {
    position: absolute; left: 0; top: 266px; width: 100%; height: 34px;
    background: var(--brand-red);
    color: var(--ink-white);
    font-size: 12px; letter-spacing: 3px;
    display: flex; align-items: center; justify-content: center;
  }

  .card-back .brand { left: 36px; top: 128px; }
  .card-back .brand-dot { width: 53px; height: 53px; margin-right: 10px; }
  .card-back .brand-name { font-size: 35px; }

  .back-stripe { position: absolute; top: 0; height: 100%; width: 3px; background: var(--brand-red); }
  .back-stripe.s1 { left: 242px; }
  .back-stripe.s2 { left: 247px; }
  .contact-panel {
    position: absolute; left: 253px; top: 0; width: 248px; height: 100%;
    background: var(--brand-red);
    color: var(--ink-white);
    padding-left: 33px;
  }
  .person-name { position: absolute; top: 75px; font-size: 17px; font-weight: 900; }
  .person-role { position: absolute; top: 97px; font-size: 12px; opacity: .92; }
  .address { position: absolute; top: 133px; font-size: 13px; font-weight: 700; line-height: 16px; }
  .contact-line { position: absolute; display: flex; align-items: center; font-size: 13px; white-space: nowrap; }
  .contact-line.phone { top: 191px; }
  .contact-line.email { top: 215px; }
  .contact-icon { width: 17px; height: 17px; margin-right: 8px; flex: none; }
</style>
</head>
<body>
  <section class="card card-front">
    <div class="brand">
      <span class="brand-dot"></span>
      <span class="brand-name">Quorva</span>
    </div>
    <div class="front-stripe thin-1"></div>
    <div class="front-stripe thin-2"></div>
    <div class="front-band">www.quorvawebsite.com</div>
  </section>

  <section class="card card-back">
    <div class="brand">
      <span class="brand-dot"></span>
      <span class="brand-name">Quorva</span>
    </div>
    <div class="back-stripe s1"></div>
    <div class="back-stripe s2"></div>
    <div class="contact-panel">
      <div class="person-name">Marcus Hale</div>
      <div class="person-role">Owner &amp; Founder</div>
      <div class="address">4172 Marlowe blvd,<br>Halden City, CA 90299</div>
      <div class="contact-line phone">
        <svg class="contact-icon" viewBox="0 0 20 20" aria-hidden="true">
          <circle cx="10" cy="10" r="10" fill="#fff"/>
          <path d="M5 8.5c0-1.5 2.2-2.5 5-2.5s5 1 5 2.5l-1.6.6-.8-1.4c-1.6-.4-3.6-.4-5.2 0l-.8 1.4z" fill="#b31d2b"/>
          <rect x="6.5" y="9.5" width="7" height="4.5" rx="1" fill="#b31d2b"/>
        </svg>
        <span>(555) 014-7396</span>
      </div>
      <div class="contact-line email">
        <svg class="contact-icon" viewBox="0 0 20 20" aria-hidden="true">
          <circle cx="10" cy="10" r="10" fill="#fff"/>
          <rect x="5" y="6.5" width="10" height="7" fill="#b31d2b"/>
          <path d="M5.3 6.8 10 10.6l4.7-3.8" fill="none" stroke="#fff" stroke-width="1"/>
        </svg>
        <span>MarcusH@quorvaweb.com</span>
      </div>
    </div>
  </section>
</body>
</html>
```